Vornel Wellness Business Card

A Double Sided Business Card

I am a private company in Melbourne, Australia, working in the Health industry. I am a nutritionist and lifestyle coach, whom specialises in using raw foods ie. fruits/nuts/vegetables to help heal my clients and enable them to achieve their ultimate state of health.

I want a sophisticated design and colour for my card that appeals to both men and women from teenage through to elderly.

Front of Card:

Red apple peel spiral in the shape of an apple. I would like a leaf/leaves coming off the stem of the apple. Please see attachments for example.

***On Right Hand side of Image is business Name: Vornel Wellness

Underneath LOGO use slogan " Let Food Be Your Medicine"

***Use Deep Red and Blues for Text Colouring

Back of Card:

Marisol Dekkert
Nutritional Specialist and Lifestyle Coach

Specialising in: Diseased Conditions
Weight Management
Achieving your Ultimate State of Health

enquiries@vornelwellness.com.au 0457 396 504

**Make sure the front design of the card flows onto the back.
Updates

Email address has been amended, Also more specific details have been given for apple peel Image, and another image attached as example of Leaf on stem of apple.

I little more insight into what sort of feel were trying to create. We're apart of the health industry, and we want the card to have a medical/clinical feeling about it.

Target Market(s)

Males and Females from teenages to elderly

Industry/Entity Type

Business

Requirements
Must have
• Red Apple Peel Spiral, in the shape of an apple, with a leaf/leaves attached to stem.
***Must be in the shape of an apple
***Please use coloring on inside of apple peel to resemble inside of an apple.
Nice to have
• I would like my card to have a clinical feel.
Should not have
• We don't want the image of the apple to look like a Christmas decoration

```html
<!DOCTYPE html>
<html lang="en">
<head>
<meta charset="utf-8">
<title>Vornel Wellness Business Card</title>
<link rel="stylesheet" href="https://fonts.googleapis.com/css2?family=Quicksand:wght@400;500;600;700&display=swap">
<style>
  :root {
    --page-bg: #ecebe8;
    --card-white: #ffffff;
    --card-grey: #d6d6d6;
    --band-grey: #a9a9a9;
    --stripe-grey: #8f8f8f;
    --deep-red: #c8231f;
    --deep-blue: #2f3f9a;
    --text-grey: #6d6d6d;
    --apple-red: #c9221d;
    --apple-light: #f2dede;
  }
  * { box-sizing: border-box; margin: 0; padding: 0; }
  html, body { width: 1200px; height: 900px; overflow: hidden; }
  body {
    background: var(--page-bg);
    font-family: "Quicksand", sans-serif;
    position: relative;
  }
  .card {
    position: absolute;
    width: 620px;
    height: 370px;
    overflow: hidden;
    box-shadow: 0 6px 18px rgba(0,0,0,.22);
  }
  /* Back of card */
  .card-back {
    left: 40px; top: 110px;
    background: radial-gradient(ellipse at 45% 35%, var(--card-white) 30%, var(--card-grey) 100%);
  }
  .stripes { position: absolute; left: 22px; top: 0; display: flex; gap: 6px; }
  .stripes span { width: 9px; height: 130px; background: var(--stripe-grey); }
  .stripes span:nth-child(3) { width: 12px; }
  .identity { position: absolute; left: 68px; top: 45px; }
  .person-name { color: var(--deep-red); font-size: 28px; font-weight: 500; line-height: 1.1; }
  .role { color: var(--text-grey); font-size: 19px; font-weight: 500; line-height: 1.2; }
  .specialities { position: absolute; left: 76px; top: 158px; }
  .specialities h2 { color: var(--deep-blue); font-size: 19px; font-weight: 600; margin-bottom: 4px; }
  .specialities li { list-style: none; color: var(--text-grey); font-size: 16.5px; font-weight: 500; line-height: 1.5; }
  .apple-area {
    position: absolute; left: 440px; top: 40px; width: 135px; height: 150px;
    border-radius: 50%;
    background: radial-gradient(circle at 40% 40%, var(--apple-light), var(--apple-red) 70%);
  }
  .contact-band {
    position: absolute; left: 0; bottom: 0; width: 100%; height: 100px;
    background: linear-gradient(var(--band-grey), #9c9c9c);
    padding: 20px 0 0 30px;
  }
  .contact-row { display: flex; align-items: center; gap: 12px; color: #fff; font-size: 18px; font-weight: 500; height: 34px; }
  .contact-row svg { width: 20px; height: 20px; }
  /* Front of card */
  .card-front {
    left: 540px; top: 445px;
    background: linear-gradient(180deg, var(--card-white) 0%, #f1f1f1 55%, var(--card-grey) 100%);
  }
  .waves { position: absolute; left: 0; top: 0; width: 100%; height: 100%; }
  .logo-circle {
    position: absolute; left: 100px; top: 112px; width: 120px; height: 120px;
    border-radius: 50%; background: var(--deep-red);
  }
  .brand { position: absolute; left: 240px; top: 140px; }
  .brand-name { color: var(--deep-red); font-size: 40px; font-weight: 600; line-height: 1; }
  .slogan { color: var(--deep-blue); font-size: 21px; font-weight: 600; margin-top: 4px; }
</style>
</head>
<body>
  <section class="card card-back">
    <div class="stripes"><span></span><span></span><span></span></div>
    <div class="identity">
      <h1 class="person-name">Marisol Dekkert</h1>
      <p class="role">Nutritional Specialist</p>
      <p class="role">Lifestyle Coach</p>
    </div>
    <div class="specialities">
      <h2>Specialising in:</h2>
      <ul>
        <li>Diseased Conditions</li>
        <li>Weight Management</li>
        <li>Achieving your Ultimate State of Health</li>
      </ul>
    </div>
    <div class="apple-area" role="img" aria-label="Red apple peel spiral shaped as an apple with leaf on stem"></div>
    <div class="contact-band">
      <div class="contact-row">
        <svg viewBox="0 0 20 20" fill="none" stroke="#fff" stroke-width="1.4"><circle cx="10" cy="10" r="8"/><ellipse cx="10" cy="10" rx="3.5" ry="8"/><line x1="2" y1="10" x2="18" y2="10"/><line x1="3.5" y1="6" x2="16.5" y2="6"/><line x1="3.5" y1="14" x2="16.5" y2="14"/></svg>
        <span>info@vornelwellness.com.au</span>
      </div>
      <div class="contact-row">
        <svg viewBox="0 0 20 20" fill="#fff"><path d="M5 2c1 0 2.5 3 2.5 4S6 7.5 6 8.5s3 4.5 4.5 5.5c1 0 1.5-1.5 2.5-1.5s4 1.5 4 2.5-2 3-3.5 3C8 18 2 12 2 5.5 2 4 4 2 5 2z"/></svg>
        <span>0457 396 504</span>
      </div>
    </div>
  </section>

  <section class="card card-front">
    <svg class="waves" viewBox="0 0 620 370" preserveAspectRatio="none">
      <path d="M0 290 C150 250 330 250 620 210 L620 370 L0 370 Z" fill="#dcdcdc"/>
      <path d="M0 310 C200 280 400 290 620 250 L620 370 L0 370 Z" fill="#cfcfcf"/>
      <path d="M330 0 C420 60 520 40 620 80 L620 0 Z" fill="#f6f6f6"/>
    </svg>
    <div class="logo-circle"></div>
    <div class="brand">
      <p class="brand-name">Vornel Wellness</p>
      <p class="slogan">Let Food Be Your Medicine</p>
    </div>
  </section>
</body>
</html>
```